Harbourline Physiotherapy business card design

We need a fresh, new business card design for our physiotherapy clinic Harbourline Physiotherapy

Will attach logo soon we had logo designed from our last project

Industry/Entity Type

Physical Therapy

Contact Information for Business Card

On front
Needs our logo, contact details:
58 Wexley Lane Bramford NSW 2790
Ph/f: 02 9481 2057
info@harbourlinephysio.example.com.au

Requirements
Must have
• On the back of the card needs to have area to write down follow up appointments
• On front
• Needs our logo
• The colours have to be the colours in our logo which are: sky blue, black and white
• Font to be same as our logo please
• We want the card to look simple, not too cluttered but to the point
Should not have
• We don't need any extra pictures other than our logo

```html
<!DOCTYPE html>
<html lang="en">
<head>
<meta charset="utf-8">
<title>Harbourline Physiotherapy – Business Card</title>
<link rel="stylesheet" href="https://fonts.googleapis.com/css2?family=Source+Sans+3:ital,wght@0,400;0,600;1,400&display=swap">
<style>
  :root {
    --page: #e9eaec;
    --card: #ffffff;
    --brand-blue: #1d6fc4;
    --ink: #3d3d3d;
    --dots: #2a78c8;
    --faint: #eef1f6;
  }
  * { box-sizing: border-box; margin: 0; padding: 0; }
  html, body { width: 1105px; height: 1200px; overflow: hidden; }
  body {
    background: var(--page);
    font-family: "Source Sans 3", sans-serif;
    position: relative;
  }
  .card {
    position: absolute;
    left: 196px;
    width: 720px;
    height: 412px;
    background: var(--card);
    border-radius: 22px;
    overflow: hidden;
  }
  .card--front { top: 146px; }
  .card--back { top: 602px; }

  /* Front */
  .brand {
    position: absolute;
    left: 34px;
    top: 112px;
    display: flex;
    align-items: center;
    gap: 14px;
  }
  .brand__dot {
    width: 34px; height: 34px;
    border-radius: 50%;
    background: var(--brand-blue);
  }
  .brand__name {
    color: var(--brand-blue);
    font-weight: 600;
    font-size: 34px;
    line-height: 1.05;
  }
  .brand-glow {
    position: absolute;
    right: 70px;
    top: 36px;
    width: 190px; height: 190px;
    border-radius: 50%;
    background: var(--faint);
  }
  .contact {
    position: absolute;
    left: 90px;
    top: 222px;
    color: var(--ink);
    font-size: 19px;
    line-height: 29px;
  }
  .contact__address { margin-bottom: 10px; }
  .contact__label { color: var(--brand-blue); font-weight: 600; margin-right: 6px; }
  .person {
    position: absolute;
    right: 30px;
    top: 262px;
    text-align: right;
  }
  .person__name { color: var(--brand-blue); font-size: 27px; font-weight: 400; line-height: 34px; }
  .person__role { color: var(--ink); font-size: 20px; line-height: 26px; }

  /* Back */
  .appointment__title {
    position: absolute;
    top: 30px; left: 0; right: 0;
    text-align: center;
    color: var(--brand-blue);
    font-size: 27px;
    font-weight: 600;
  }
  .field {
    position: absolute;
    display: flex;
    align-items: baseline;
    color: var(--brand-blue);
    font-size: 20px;
  }
  .field__label { margin-right: 10px; white-space: nowrap; }
  .field__line {
    flex: 1;
    border-bottom: 2px dotted var(--dots);
    height: 1px;
  }
  .field__suffix { font-size: 15px; margin-left: 8px; }
  .field--name { left: 37px; right: 58px; top: 95px; }
  .field--date { left: 34px; width: 355px; top: 162px; }
  .field--time { left: 400px; right: 58px; top: 162px; }
  .field--note { left: 37px; right: 63px; top: 222px; }
  .rule {
    position: absolute;
    left: 36px; right: 63px;
    border-bottom: 2px dotted var(--dots);
  }
  .rule--1 { top: 276px; }
  .rule--2 { top: 316px; }
  .appointment__notice {
    position: absolute;
    top: 338px; left: 0; right: 0;
    text-align: center;
    color: var(--brand-blue);
    font-style: italic;
    font-size: 15px;
    line-height: 20px;
  }
</style>
</head>
<body>
  <section class="card card--front">
    <div class="brand-glow" aria-hidden="true"></div>
    <div class="brand">
      <span class="brand__dot" aria-hidden="true"></span>
      <span class="brand__name">Harbourline<br>Physiotherapy</span>
    </div>
    <div class="contact">
      <p class="contact__address">58 Wexley Lane Bramford<br>NSW 2790</p>
      <p><span class="contact__label">Ph/Fax</span>02 9481 2057</p>
      <p>info@harbourlinephysio.example.com.au</p>
      <p>www.harbourlinephysio.example.com.au</p>
    </div>
    <div class="person">
      <p class="person__name">Daniel Brooke</p>
      <p class="person__role">CEO/Founder</p>
    </div>
  </section>

  <section class="card card--back">
    <h2 class="appointment__title">Next Appointment</h2>
    <div class="field field--name"><span class="field__label">Name :</span><span class="field__line"></span></div>
    <div class="field field--date"><span class="field__label">Date :</span><span class="field__line"></span></div>
    <div class="field field--time"><span class="field__label">Time :</span><span class="field__line"></span><span class="field__suffix">AM/PM</span></div>
    <div class="field field--note"><span class="field__label">Note :</span><span class="field__line"></span></div>
    <div class="rule rule--1"></div>
    <div class="rule rule--2"></div>
    <p class="appointment__notice">Please give me 24 hours notice if you are unable to keep your appointment or<br>a cancellation fee may be charged.</p>
  </section>
</body>
</html>
```